Business Card Design Project

We need a Business Card for an Mechanical Engineering firm in Singapore. The design should be Modern & Technical looking, yet eye catching.

Our company deals in Cutting Tools & Machine Accessories for the Manufacturing Industries such as Oil & Gas, Aero Space, etc... For more information on our Company, you can either email me or view our website www.torvalen.com.sg.

We are trying to revamp our image to give our consumers a fresh new perspective to our company, so we welcome all ideas.

Industry/Entity Type

Business

Requirements
Must have
• Must incorporate New Company Logo into the card as shown in Uploaded file.

```html
<!DOCTYPE html>
<html lang="en">
<head>
<meta charset="utf-8">
<title>Torvalen Tools – Business Card</title>
<link rel="stylesheet" href="https://fonts.googleapis.com/css2?family=Open+Sans:wght@400;700&family=Dancing+Script:wght@700&display=swap">
<style>
  :root {
    --brand-red: #9b1238;
    --text-maroon: #4a1530;
    --card-white: #ffffff;
  }
  html, body {
    margin: 0;
    padding: 0;
    width: 710px;
    height: 1200px;
    overflow: hidden;
    background: var(--card-white);
  }
  .business-card {
    position: relative;
    width: 710px;
    height: 1200px;
    background: var(--card-white);
    color: var(--text-maroon);
    font-family: "Open Sans", sans-serif;
    text-align: center;
  }
  .brand-mark {
    position: absolute;
    top: 250px;
    left: 0;
    width: 100%;
    display: flex;
    justify-content: center;
    align-items: center;
    gap: 22px;
  }
  .brand-dot {
    width: 44px;
    height: 44px;
    border-radius: 50%;
    background: var(--brand-red);
  }
  .brand-name {
    margin: 0;
    font-size: 60px;
    font-weight: 700;
    letter-spacing: 1px;
    color: var(--brand-red);
    line-height: 1;
  }
  .company-details {
    position: absolute;
    top: 480px;
    left: 0;
    width: 100%;
  }
  .company-name {
    margin: 0 0 6px;
    font-size: 42px;
    font-weight: 700;
    line-height: 1.25;
  }
  .address, .contact-lines {
    margin: 0;
    font-size: 32px;
    font-weight: 400;
    line-height: 52px;
    font-style: normal;
  }
  .contact-lines {
    margin-top: 52px;
  }
  .contact-person {
    position: absolute;
    top: 1062px;
    left: 0;
    width: 100%;
  }
  .contact-label {
    margin: 0;
    font-size: 25px;
    line-height: 1.2;
  }
  .contact-name {
    margin: 6px 0 0;
    font-family: "Dancing Script", cursive;
    font-size: 54px;
    font-weight: 700;
    line-height: 1.1;
  }
</style>
</head>
<body>
  <main class="business-card">
    <div class="brand-mark">
      <span class="brand-dot" aria-hidden="true"></span>
      <p class="brand-name">TORVALEN TOOLS</p>
    </div>

    <section class="company-details">
      <h1 class="company-name">Torvalen Tools Pte Ltd</h1>
      <address class="address">
        27 Kallang Crescent #03-08,<br>
        Meridian Industrial Hub,<br>
        Singapore 339411
      </address>
      <p class="contact-lines">
        Tel: 65-63150247<br>
        Fax: 65-63150248<br>
        Email: hello@torvalen.com.sg<br>
        Website: www.torvalen.com.sg
      </p>
    </section>

    <section class="contact-person">
      <p class="contact-label">Contact Person</p>
      <p class="contact-name">Marissa</p>
    </section>
  </main>
</body>
</html>
```